Spiritual Healing bussiness needs logo/business card

Simple, clean looking logo/card
For spiritual business with healing services and occult rituals

Contact Information for Business Card

Needs my name: Tobin Varley
Business name: Lantern Healing Shop
Services provided and worded in this way:

Reiki Healing
Tarot
Oils
Rituals Of Change

Can look occult like but with light energy.

Colors
0255a3
3276b5
85abd2
33a6d7
85cae6
0292cd

```html
<!DOCTYPE html>
<html lang="en">
<head>
<meta charset="utf-8">
<title>Lantern Healing Shop — Business Card</title>
<link rel="stylesheet" href="https://fonts.googleapis.com/css2?family=Bitter:wght@400;500&family=Lato:wght@400&display=swap">
<style>
  :root {
    --page-bg: #e9ecef;
    --deep-blue: #0255a3;
    --sky-blue: #0292cd;
    --seal-white: #f3f5f7;
    --text-light: #ffffff;
  }
  * { margin: 0; padding: 0; box-sizing: border-box; }
  html, body {
    width: 1200px;
    height: 900px;
    overflow: hidden;
    background: var(--page-bg);
  }
  .card {
    position: absolute;
    left: 120px;
    top: 153px;
    width: 960px;
    height: 593px;
    background: var(--deep-blue);
    overflow: hidden;
    box-shadow: 0 10px 30px rgba(0, 0, 0, 0.15);
  }
  .card__accent-band {
    position: absolute;
    left: 675px;
    top: 0;
    width: 285px;
    height: 100%;
    background: var(--sky-blue);
  }
  .card__seal {
    position: absolute;
    left: 422px;
    top: 33px;
    width: 516px;
    height: 516px;
    border-radius: 50%;
    background: var(--seal-white);
  }
  .brand {
    position: absolute;
    left: 422px;
    top: 33px;
    width: 516px;
    height: 516px;
    text-align: center;
  }
  .brand__mark {
    position: absolute;
    left: 50%;
    top: 121px;
    width: 170px;
    height: 170px;
    margin-left: -85px;
    border: 9px solid var(--deep-blue);
    border-radius: 50%;
  }
  .brand__name {
    position: absolute;
    left: 0;
    right: 0;
    top: 306px;
    font-family: "Bitter", serif;
    font-weight: 500;
    font-size: 37px;
    color: var(--deep-blue);
    letter-spacing: 0.3px;
  }
  .owner-name {
    position: absolute;
    left: 59px;
    top: 66px;
    font-family: "Bitter", serif;
    font-weight: 400;
    font-size: 38px;
    color: var(--text-light);
    letter-spacing: 0.5px;
  }
  .contact-list {
    position: absolute;
    left: 57px;
    top: 160px;
    list-style: none;
    font-family: "Lato", sans-serif;
    font-size: 27px;
    color: var(--text-light);
  }
  .contact-list__item {
    display: flex;
    align-items: center;
    height: 38px;
  }
  .contact-list__icon {
    width: 31px;
    height: 31px;
    margin-right: 6px;
    flex: none;
  }
  .service-list {
    position: absolute;
    left: 56px;
    top: 386px;
    list-style: none;
    font-family: "Lato", sans-serif;
    font-size: 27px;
    color: var(--text-light);
  }
  .service-list__item {
    display: flex;
    align-items: center;
    height: 36.5px;
  }
  .service-list__item::before {
    content: "";
    width: 14px;
    height: 14px;
    border-radius: 50%;
    background: var(--text-light);
    margin-right: 6px;
    flex: none;
  }
</style>
</head>
<body>
  <div class="card">
    <div class="card__accent-band"></div>
    <div class="card__seal"></div>

    <div class="brand">
      <div class="brand__mark"></div>
      <div class="brand__name">Lantern Healing Shop</div>
    </div>

    <h1 class="owner-name">Tobin Varley</h1>

    <ul class="contact-list">
      <li class="contact-list__item">
        <svg class="contact-list__icon" viewBox="0 0 32 32" aria-hidden="true">
          <circle cx="16" cy="16" r="14.5" fill="none" stroke="#fff" stroke-width="2"/>
          <path d="M8 14c0-3 3.5-4.5 8-4.5s8 1.5 8 4.5v1.2h-3.6v-2.2h-8.8v2.2H8z" fill="#fff"/>
          <path d="M10.5 23l1.8-6.5h7.4l1.8 6.5z" fill="#fff"/>
          <circle cx="16" cy="19.6" r="1.6" fill="#0255a3"/>
        </svg>
        <span>044-987 654 321</span>
      </li>
      <li class="contact-list__item">
        <svg class="contact-list__icon" viewBox="0 0 32 32" aria-hidden="true">
          <circle cx="16" cy="16" r="14.5" fill="none" stroke="#fff" stroke-width="2"/>
          <rect x="8" y="10.5" width="16" height="11" rx="1" fill="#fff"/>
          <path d="M8.5 11.2L16 17l7.5-5.8" fill="none" stroke="#0255a3" stroke-width="1.5"/>
        </svg>
        <span>hello@lanternhealing.com</span>
      </li>
    </ul>

    <ul class="service-list">
      <li class="service-list__item">Reiki Healing</li>
      <li class="service-list__item">Tarot</li>
      <li class="service-list__item">Oils</li>
      <li class="service-list__item">Rituals Of Change</li>
    </ul>
  </div>
</body>
</html>
```